Beef cattle farm needs signs which can be seen from roadside

We would like submissions of artwork for a sign that will hang from a fence or gate and will be seen by passing cars.

Existing logo and branding theme for the company is attached.

Signage can be between 900mm x 400mm - 1200mm x 600mm

Industry/Entity Type

Farm

Requirements
Must have
• the Signs should have the following information:
• Company name: Wendlow Grazing Company
• Address: 417 Corrigan Flat Road
• Contact number: 0431 862 407
• email address: admin@wendlowgrazingcompany.com.au
• - Logo and branding as per attached artwork

```html
<!DOCTYPE html>
<html lang="en">
<head>
<meta charset="utf-8">
<title>Wendlow Grazing Company – Roadside Signs</title>
<link rel="stylesheet" href="https://fonts.googleapis.com/css2?family=Montserrat:wght@500;600&display=swap">
<style>
  :root {
    --farm-green: #2a6e47;
    --paper: #ffffff;
    --backdrop: #c9c9c9;
    --ink-light: #ffffff;
  }
  * { margin: 0; padding: 0; box-sizing: border-box; }
  html, body {
    width: 1058px; height: 1200px; overflow: hidden;
    background: var(--backdrop);
    font-family: "Montserrat", sans-serif;
  }
  .sign {
    position: absolute; left: 116px; width: 826px; height: 412px;
    overflow: hidden;
  }
  .sign--light { top: 119px; background: var(--paper); }
  .sign--dark { top: 654px; background: var(--farm-green); }

  .band {
    position: absolute; left: 0; width: 100%;
    background: var(--farm-green); color: var(--ink-light);
    display: flex; align-items: center; justify-content: center;
    font-weight: 500; white-space: nowrap;
  }
  .band--top { top: 0; height: 68px; font-size: 35px; }
  .band--bottom { bottom: 0; height: 67px; font-size: 35px; }
  .band .divider {
    display: inline-block; width: 2px; height: 44px;
    background: var(--ink-light); margin: 0 14px;
  }

  .rule {
    position: absolute; left: 0; width: 100%; height: 3px;
    background: var(--paper);
  }
  .rule--top { top: 70px; }
  .rule--bottom { top: 340px; }

  .brand-dot {
    position: absolute; border-radius: 50%;
    width: 228px; height: 228px;
  }
  .sign--light .brand-dot { left: 48px; top: 100px; background: var(--farm-green); }
  .sign--dark .brand-dot { left: 40px; top: 88px; background: var(--paper); }

  .brand-name {
    position: absolute; left: 296px; width: 490px;
    font-weight: 600; text-align: center; line-height: 1;
    white-space: nowrap;
  }
  .sign--light .brand-name { top: 171px; color: var(--farm-green); }
  .sign--dark .brand-name { top: 178px; color: var(--ink-light); }
  .brand-name .main { display: block; font-size: 80px; letter-spacing: 0; }
  .brand-name .sub { display: block; font-size: 41px; margin-top: 16px; letter-spacing: 0.5px; }

  .phone-line {
    position: absolute; left: 296px; width: 490px; top: 86px;
    text-align: center; color: var(--ink-light);
    font-size: 46px; font-weight: 500; white-space: nowrap;
  }
</style>
</head>
<body>

<section class="sign sign--light" aria-label="Roadside sign, white version">
  <div class="band band--top">417 Corrigan Flat Road<span class="divider"></span>0431 862 407</div>
  <div class="brand-dot"></div>
  <h1 class="brand-name"><span class="main">WENDLOW</span><span class="sub">GRAZING COMPANY</span></h1>
  <div class="band band--bottom">admin@wendlowgrazingcompany.com.au</div>
</section>

<section class="sign sign--dark" aria-label="Roadside sign, green version">
  <div class="band band--top">417 Corrigan Flat Road</div>
  <div class="rule rule--top"></div>
  <div class="brand-dot"></div>
  <p class="phone-line">0431 862 407</p>
  <h2 class="brand-name"><span class="main">WENDLOW</span><span class="sub">GRAZING COMPANY</span></h2>
  <div class="rule rule--bottom"></div>
  <div class="band band--bottom">admin@wendlowgrazingcompany.com.au</div>
</section>

</body>
</html>
```